Web design for financial services

A modern web design of financial services (brokerage firm)
Req.s and technology tags :
- Very mobile friendly.
- One paged with some inner pages.
- Animated sticky header .
- Member login area for e-trade.
- Support RTL language.
- HTML & CSS.

The logo will be Home link
• MPTR :
WHO WE ARE
Content :
i) Board of Directors
ii) Mission Statement
iii) Corporate Values
iv) Regulations
• Financial Services :
WHAT WE DO
Content:
i) Electronic trading
ii) Trading desk
iii) Institutional
iv) Investors Education
• News
• Market Tools
• Forms---- opens new page
• Careers---- opens new page
• Contact Us----opens new page

The website is :
http://www.mptr-doha-example.com/

The logo need some changes to be more modern and impressively , but with keeping same structure .

Some related websites :
https://www.lv-bourse.example/

financial market

Financial Service

Coded - Design and coding required

2 page

• same fonts of http://www.kwdholdings.example/

• - Very mobile friendly.
• - One paged with some inner pages.
• - Animated sticky header .
• - Member login area for e-trade.
• - Support RTL language.
• - HTML & CSS.
• Slider , some Qatari theme,
• i like the video inside the home page
• ex :http://www.kwdholdings.example/

```html
<!DOCTYPE html>
<html lang="en">
<head>
<meta charset="utf-8">
<title>MPTR – Financial Services</title>
<link rel="stylesheet" href="https://fonts.googleapis.com/css2?family=Ubuntu:wght@400;500;700&family=Open+Sans:wght@400;600;700&display=swap">
<style>
:root{
  --brand:#9b2a24;
  --brand-dark:#7e1f1a;
  --ink:#222222;
  --muted:#8a8a8a;
  --line:#e3e3e3;
  --soft:#f6f6f6;
  --footer:#efefef;
  --white:#ffffff;
}
*{box-sizing:border-box;margin:0;padding:0}
html,body{width:1200px;height:3502px;overflow:hidden}
body{position:relative;background:var(--white);font-family:"Open Sans",Arial,sans-serif;color:var(--ink)}
a{color:inherit;text-decoration:none}

/* header */
.site-header{position:absolute;left:0;top:0;width:1200px;height:121px;background:var(--white)}
.brand{position:absolute;left:172px;top:38px;display:flex;align-items:center;gap:10px;font-family:"Ubuntu",sans-serif;font-weight:700;font-size:26px;color:var(--brand)}
.brand-mark{width:22px;height:22px;background:var(--brand)}
.login{position:absolute;left:832px;top:32px;width:84px;height:22px;background:var(--brand);color:#fff;font-size:12px;font-weight:600;display:flex;align-items:center;justify-content:center;gap:6px}
.lang{position:absolute;left:944px;top:34px;font-size:13px;display:flex;align-items:center;gap:8px}
.flag{width:20px;height:13px;background:linear-gradient(#c8102e 0 50%,#fff 50%);border:1px solid #ddd}
.main-nav{position:absolute;top:76px;left:0;font-family:"Ubuntu",sans-serif;font-size:13px;font-weight:500;text-transform:uppercase}
.main-nav a{position:absolute;white-space:nowrap}

/* hero */
.hero{position:absolute;left:0;top:121px;width:1200px;height:551px;background:linear-gradient(160deg,#3c5366 0%,#6c7f8c 35%,#8a6a4c 70%,#2c3440 100%)}
.hero-title{position:absolute;left:0;right:0;top:250px;text-align:center;color:#fff;font-family:"Ubuntu",sans-serif;font-weight:700;font-size:27px;letter-spacing:.5px}
.hero-arrow{position:absolute;top:270px}

/* who we are */
.about{position:absolute;left:0;top:672px;width:1200px;height:563px}
.about-photo{position:absolute;left:672px;top:0;width:528px;height:563px;background:linear-gradient(135deg,#d8d2c6 0%,#9f8e78 45%,#5a4a3a 100%)}
.section-title{font-family:"Ubuntu",sans-serif;font-weight:700;color:var(--ink)}
.about .section-title{position:absolute;left:172px;top:88px;font-size:44px}
.body-text{font-size:13px;line-height:23px;color:var(--muted)}
.about .body-text{position:absolute;left:172px;top:188px;width:450px}
.btn{position:absolute;height:44px;border-radius:22px;background:var(--brand);color:#fff;font-family:"Ubuntu",sans-serif;font-size:13px;font-weight:500;display:flex;align-items:center;justify-content:center;text-transform:uppercase}
.about .btn{left:172px;top:418px;width:195px}

/* what we do */
.services-band{position:absolute;left:0;top:1235px;width:1200px;height:356px;background:linear-gradient(90deg,#7e2a25 0%,#b0514a 50%,#9b3a33 100%)}
.services-band h2{position:absolute;left:0;right:0;top:150px;text-align:center;color:#fff;font-family:"Ubuntu",sans-serif;font-weight:700;font-size:42px}
.services-text{position:absolute;left:172px;top:1656px;width:856px;text-align:center}
.services-btn{left:509px;top:1829px;width:194px}

/* news */
.news{position:absolute;left:0;top:1953px;width:1200px;height:744px;background:var(--soft)}
.news .section-title{position:absolute;left:0;right:0;top:56px;text-align:center;font-size:44px}
.news-card{position:absolute;top:186px;width:268px;height:500px}
.news-photo{width:268px;height:168px}
.news-date{margin-top:38px;font-size:12px;font-weight:700;text-transform:uppercase}
.news-title{margin-top:20px;font-family:"Ubuntu",sans-serif;font-size:19px;font-weight:400;line-height:24px;color:var(--ink)}
.news-excerpt{margin-top:6px;font-size:12px;line-height:21px;color:var(--muted)}
.btn-outline{position:absolute;top:458px;left:0;width:130px;height:36px;border:1px solid #bbb;border-radius:18px;background:#fff;font-size:13px;display:flex;align-items:center;justify-content:center}

/* partners */
.partners{position:absolute;left:172px;top:2697px;width:856px;height:116px;border-bottom:1px solid var(--line);display:flex;align-items:center;justify-content:space-between;font-family:"Ubuntu",sans-serif;color:#333}
.partners span{font-size:22px;font-weight:400}

/* market tool */
.market .section-title{position:absolute;left:0;right:0;top:2862px;text-align:center;font-size:46px;color:var(--brand)}
.tool{position:absolute;top:2962px;width:268px;text-align:center}
.tool-label{font-size:12px;font-weight:700;text-transform:uppercase}
.tool-box{margin-top:16px;height:98px;border:1px solid var(--line);background:#fff;display:flex;align-items:center;justify-content:center;font-family:"Ubuntu",sans-serif;font-weight:500;font-size:24px;color:#111}

/* footer */
.site-footer{position:absolute;left:0;top:3162px;width:1200px;height:289px;background:var(--footer)}
.footer-brand{left:170px;top:68px}
.footer-col{position:absolute;top:70px;font-size:11px;color:#444}
.footer-col h4{font-family:"Ubuntu",sans-serif;font-size:13px;color:var(--brand);font-weight:500;margin-bottom:22px}
.footer-col li{list-style:none;line-height:23px;display:flex;gap:12px}
.footer-col li::before{content:"›";color:#666}
.contact-row{display:flex;gap:12px;line-height:21px;margin-bottom:12px}
.contact-row svg{flex:none;margin-top:4px}
.copyright{position:absolute;left:0;top:3451px;width:1200px;height:51px;border-top:1px solid #ddd;background:#fff;font-size:11px;display:flex;align-items:center;justify-content:center}
</style>
</head>
<body>

<header class="site-header">
  <a class="brand" href="#"><span class="brand-mark"></span>MPTR</a>
  <a class="login" href="#">
    <svg width="9" height="10" viewBox="0 0 9 10"><rect x="1" y="4" width="7" height="6" fill="#fff"/><path d="M2.5 4V2.5a2 2 0 0 1 4 0V4" stroke="#fff" fill="none"/></svg>LOGIN</a>
  <div class="lang"><span class="flag"></span>English <span style="font-size:9px">▾</span></div>
  <nav class="main-nav">
    <a href="#" style="left:406px">MPTR</a>
    <a href="#" style="left:481px">Financial Services</a>
    <a href="#" style="left:657px">News</a>
    <a href="#" style="left:741px">Market Tool</a>
    <a href="#" style="left:880px">Forms</a>
    <a href="#" style="left:971px">Careers</a>
  </nav>
</header>

<section class="hero" role="img" aria-label="City skyline with glass towers and a walkway bridge">
  <svg class="hero-arrow" style="left:62px" width="16" height="30" viewBox="0 0 16 30"><path d="M14 2 2 15l12 13" stroke="#fff" stroke-width="2" fill="none"/></svg>
  <h1 class="hero-title">MERIDIAN PORT TRADING RESOURCES .CO</h1>
  <svg class="hero-arrow" style="left:1122px" width="16" height="30" viewBox="0 0 16 30"><path d="M2 2l12 13L2 28" stroke="#fff" stroke-width="2" fill="none"/></svg>
</section>

<section class="about">
  <h2 class="section-title">WHO WE ARE ?</h2>
  <p class="body-text">At vero eos et accusamus et iusto odio dignissimos ducimus qui blanditiis praesentium voluptatum deleniti atque corrupti quos dolores et quas molestias excepturi sint occaecati cupiditate non provident, similique sunt in culpa qui officia deserunt mollitia animi, id est laborum et dolorum fuga. Et harum quidem rerum facilis est et expedita distinctio. Nam libero tempore, cum soluta nobis est eligendi optio cumque nihil impedit quo minus id quod maxime placeat facere possimus</p>
  <a class="btn" href="#">About MPTR</a>
  <div class="about-photo" role="img" aria-label="Laptop with charts, coffee cup and phone on a wooden desk"></div>
</section>

<section class="services-band" role="img" aria-label="Advisers meeting with clients under a red tint">
  <h2>WHAT WE DO</h2>
</section>
<p class="body-text services-text">At vero eos et accusamus et iusto odio dignissimos ducimus qui blanditiis praesentium voluptatum deleniti atque corrupti quos dolores et quas molestias excepturi sint occaecati cupiditate non provident, similique sunt in culpa qui officia deserunt mollitia animi, id est laborum et dolorum fuga. Et harum quidem rerum facilis est et expedita distinctio. Nam libero tempore, cum soluta nobis est eligendi optio cumque nihil impedit quo minus id quod maxime placeat facere possimus, omnis voluptas assumenda est, omnis dolor repellendus. Temporibus autem quibusdam et aut officiis debitis aut rerum</p>
<a class="btn services-btn" href="#">Read More</a>

<section class="news">
  <h2 class="section-title">NEWS</h2>
  <article class="news-card" style="left:173px">
    <div class="news-photo" role="img" aria-label="Blue financial chart with rising arrow" style="background:linear-gradient(135deg,#2b5d9a,#9fc2e6)"></div>
    <p class="news-date">February 2nd &nbsp;| 2017</p>
    <h3 class="news-title">At vero eos et accusamus et iusto odio dignissimos ducimus qui blanditiis praesentium</h3>
    <p class="news-excerpt">At vero eos et accusamus et iusto odio dignissimos ducimus qui blanditiis praesentium voluptatum deleniti atque Temporibus autem quibusdam et aut officiis debitis</p>
    <a class="btn-outline" href="#">Read More</a>
  </article>
  <article class="news-card" style="left:465px">
    <div class="news-photo" role="img" aria-label="Couple meeting a financial adviser" style="background:linear-gradient(135deg,#c9b8a0,#7d6b5a)"></div>
    <p class="news-date">February 2nd &nbsp;| 2017</p>
    <h3 class="news-title">At vero eos et accusamus et iusto odio dignissimos ducimus qui blanditiis praesentium</h3>
    <p class="news-excerpt">At vero eos et accusamus et iusto odio dignissimos ducimus qui blanditiis praesentium voluptatum deleniti atque Temporibus autem quibusdam et aut officiis debitis</p>
    <a class="btn-outline" href="#">Read More</a>
  </article>
  <article class="news-card" style="left:757px">
    <div class="news-photo" role="img" aria-label="Hands holding a tablet showing market data" style="background:linear-gradient(135deg,#5a4a3e,#b8b4ae)"></div>
    <p class="news-date">February 2nd &nbsp;| 2017</p>
    <h3 class="news-title">At vero eos et accusamus et iusto odio dignissimos ducimus qui blanditiis praesentium</h3>
    <p class="news-excerpt">At vero eos et accusamus et iusto odio dignissimos ducimus qui blanditiis praesentium voluptatum deleniti atque Temporibus autem quibusdam et aut officiis debitis</p>
    <a class="btn-outline" href="#">Read More</a>
  </article>
</section>

<div class="partners">
  <span>Northvale</span>
  <span>Kestrano</span>
  <span>Graniteford</span>
  <span>Maison Civique</span>
  <span>Verdantis</span>
</div>

<section class="market">
  <h2 class="section-title">MARKET TOOL</h2>
  <div class="tool" style="left:173px"><p class="tool-label">Most Activity Company</p><div class="tool-box">Corvana Group</div></div>
  <div class="tool" style="left:465px"><p class="tool-label">Top Gainer</p><div class="tool-box">Aldermoor</div></div>
  <div class="tool" style="left:757px"><p class="tool-label">Top Loser</p><div class="tool-box">Lumen Banque</div></div>
</section>

<footer class="site-footer">
  <a class="brand footer-brand" href="#"><span class="brand-mark"></span>MPTR</a>
  <div class="footer-col" style="left:362px">
    <h4>Quick Links</h4>
    <ul><li>MPTR</li><li>Financial Services</li><li>News</li><li>Market Tool</li><li>Forms</li><li>Careers</li></ul>
  </div>
  <div class="footer-col" style="left:537px">
    <h4>Lusail Bourse Branch</h4>
    <div class="contact-row"><svg width="11" height="11" viewBox="0 0 11 11"><rect x="1" y="1" width="9" height="9" fill="var(--brand)"/></svg><span>Second Floor, Sidra Plaza,<br>Corniche Road near Harbour Square</span></div>
    <div class="contact-row"><svg width="11" height="11" viewBox="0 0 11 11"><path d="M2 1h3l1 3-2 1a6 6 0 0 0 2 2l1-2 3 1v3a1 1 0 0 1-1 1A9 9 0 0 1 1 2a1 1 0 0 1 1-1z" fill="var(--brand)"/></svg><span>Tel: +974 40001234</span></div>
    <div class="contact-row"><svg width="11" height="11" viewBox="0 0 11 11"><rect x="1" y="3" width="9" height="6" fill="var(--brand)"/><rect x="3" y="1" width="5" height="2" fill="var(--brand)"/></svg><span>Fax: +974 40005678</span></div>
  </div>
  <div class="footer-col" style="left:806px">
    <h4>Office Hours</h4>
    <div class="contact-row"><svg width="11" height="11" viewBox="0 0 11 11"><circle cx="5.5" cy="5.5" r="4.5" stroke="var(--brand)" fill="none"/><path d="M5.5 3v3h2" stroke="var(--brand)" fill="none"/></svg><span>Sunday - Thursday<br>From 8:00 AM - 3:00 PM<br>Friday and Saturday are official holiday</span></div>
  </div>
</footer>
<div class="copyright">© 2017 Company Name | All Rights Reserved</div>

</body>
</html>
```